VELMOR Website Design

We need a website designed for our company VELMOR. We are a luxury lifestyle club that will provide benefits and services for our members. The site should be clean & sleek, preferably using black and white (or darker colors). (example sites: stravenhall.example, plinth.example)

Here is a link of a sample page I did using wix. (https://dunmere7.sitehostly.example/mysite) This can be used to get a general idea.

Target Market(s)

Upper Middle Class in the United States

Number of Pages Required

5+ page

Font styles to use
Sans Serif
Other font styles liked:
• Arial (or other similar fonts)

Requirements
Must have
• A clean design that is eye-catching and speaks to our company.
Nice to have
• Ideas for copy.

```html
<!DOCTYPE html>
<html lang="en">
<head>
<meta charset="utf-8">
<title>VELMOR – A Members Only Lifestyle Club</title>
<link rel="stylesheet" href="https://fonts.googleapis.com/css2?family=Lato:wght@400;700;900&family=Roboto:wght@400;500;700&display=swap">
<style>
:root{
  --purple:#8e0f80;
  --purple-dark:#7a0a6d;
  --ink:#1b1b1b;
  --band:#1e1b1b;
  --text:#555;
  --white:#fff;
  --blush:#f6e7f3;
  --line:#d9d9d9;
}
*{box-sizing:border-box;margin:0;padding:0}
html,body{width:1200px;height:2791px;overflow:hidden}
body{position:relative;background:var(--white);font-family:'Roboto',Arial,sans-serif;color:var(--ink)}
.abs{position:absolute}
.center{left:0;width:1200px;text-align:center}

/* hero */
.hero{position:absolute;left:0;top:0;width:1200px;height:601px;
  background:linear-gradient(120deg,#4a3a33 0%,#2c2322 35%,#5a4640 60%,#2a2220 100%)}
.hero::after{content:"";position:absolute;inset:0;background:rgba(0,0,0,.35)}
.logo{position:absolute;left:97px;top:30px;font-family:'Lato',Arial,sans-serif;font-weight:700;font-size:44px;color:var(--white);letter-spacing:1px}
.nav{position:absolute;left:484px;top:46px;display:flex;gap:34px;font-family:'Roboto',Arial,sans-serif;font-weight:500;font-size:15.5px;color:var(--white)}
.btn-apply{position:absolute;left:962px;top:35px;width:138px;height:41px;background:var(--purple);color:var(--white);font-weight:500;font-size:15.5px;display:flex;align-items:center;justify-content:center}
.hero-title{top:234px;font-family:'Lato',Arial,sans-serif;font-weight:700;font-size:70px;color:var(--white)}
.hero-sub{top:322px;font-family:'Roboto',Arial,sans-serif;font-weight:500;font-size:31px;color:var(--white)}
.scroll-cue{left:571px;top:398px}

/* membership bar */
.member{position:absolute;left:99px;top:526px;width:1001px;height:148px;display:flex}
.member-lead{width:500px;background:var(--purple);color:var(--white);text-align:center;padding-top:38px}
.member-lead h2{font-family:'Lato',Arial,sans-serif;font-weight:700;font-size:37px}
.member-lead p{font-family:'Lato',Arial,sans-serif;font-size:15px;letter-spacing:2px;margin-top:6px}
.member-form{flex:1;background:var(--ink);display:flex;align-items:center;padding-left:35px}
.member-input{width:311px;height:50px;background:var(--white);color:#666;font-size:14px;display:flex;align-items:center;padding-left:18px}
.member-btn{width:128px;height:50px;background:var(--purple);color:var(--white);font-weight:700;font-size:18px;display:flex;align-items:center;justify-content:center}

/* about */
.about-photo{left:123px;top:787px;width:450px;height:331px;border:4px solid #fff;box-shadow:0 0 0 1px #ccc,0 2px 6px rgba(0,0,0,.25);
  background:linear-gradient(135deg,#c9c4bd 0%,#8c8a8a 40%,#3c3f48 65%,#b4b6bb 100%)}
.num{font-family:'Lato',Arial,sans-serif;font-weight:900;color:var(--purple);font-size:68px;line-height:1}
.kicker{font-family:'Lato',Arial,sans-serif;font-weight:700;color:var(--purple);font-size:18px;letter-spacing:.5px}
.heading{font-family:'Lato',Arial,sans-serif;font-weight:700;font-size:41px;color:var(--ink)}
.about-copy{left:642px;top:880px;width:434px;font-size:14px;line-height:26px;color:var(--text)}
.about-copy p+p{margin-top:26px}
.btn{display:flex;align-items:center;justify-content:center;gap:6px;background:var(--purple);color:var(--white);font-weight:700;font-size:16px}

/* benefits */
.benefits-band{left:0;top:1254px;width:1200px;height:416px;background:linear-gradient(90deg,#1a1717,#2b2524 50%,#1a1717)}
.pink-band{left:0;top:1670px;width:1200px;height:841px;background:linear-gradient(180deg,#f8eef6 0%,#f3e2ef 55%,#f7ecf4 100%)}
.badge{left:538px;top:1188px;width:124px;height:124px;border-radius:50%;background:var(--white);display:flex;align-items:center;justify-content:center}
.grid{left:99px;top:1576px;width:1002px;height:433px;background:var(--white);border:1px solid var(--line);display:grid;grid-template-columns:repeat(3,1fr);grid-template-rows:repeat(2,1fr)}
.cell{border-right:1px solid var(--line);border-bottom:1px solid var(--line);text-align:center;padding-top:26px}
.cell:nth-child(3n){border-right:none}
.cell:nth-child(n+4){border-bottom:none}
.cell-icon{width:84px;height:76px;margin:0 auto;border-radius:8px;background:linear-gradient(135deg,#b04aa4,var(--purple-dark))}
.cell h3{font-family:'Roboto',Arial,sans-serif;font-weight:500;font-size:21px;margin-top:14px;color:var(--ink)}
.cell p{font-size:13px;line-height:22px;color:#666;margin-top:6px}

/* footer */
.footer{left:0;top:2511px;width:1200px;height:280px;background:linear-gradient(90deg,#141313,#1f1d1d 50%,#141313)}
.socials{left:463px;top:2586px;display:flex;gap:8px}
.social{width:48px;height:48px;border-radius:50%;border:2px solid var(--white)}
.social.active{background:var(--purple)}
.foot-links{top:2674px;display:flex;justify-content:center;gap:28px;font-size:15px;color:var(--white)}
.copyright{top:2717px;font-size:15px;color:var(--white)}
</style>
</head>
<body>

<header class="hero" role="img" aria-label="Photo of smiling friends high-fiving at a social gathering"></header>
<div class="logo">VELMOR</div>
<nav class="nav"><span>HOME</span><span>ABOUT</span><span>SERVICES &amp; BENEFITS</span><span>CONTACT US</span></nav>
<div class="btn-apply">APPLY NOW</div>
<h1 class="abs center hero-title">VELMOR</h1>
<p class="abs center hero-sub">A Members Only Lifestyle Club</p>
<svg class="abs scroll-cue" width="58" height="58" viewBox="0 0 58 58" aria-hidden="true">
  <circle cx="29" cy="29" r="27" fill="none" stroke="#fff" stroke-width="2.5"/>
  <path d="M19 25 L29 35 L39 25" fill="none" stroke="#fff" stroke-width="3" stroke-linecap="round" stroke-linejoin="round"/>
</svg>

<section class="member">
  <div class="member-lead">
    <h2>VELMOR MEMBERSHIP</h2>
    <p>AMAZING BENEFITS AND SERVICES.</p>
  </div>
  <div class="member-form">
    <div class="member-input">Email Address</div>
    <div class="member-btn">JOIN NOW!</div>
  </div>
</section>

<div class="abs about-photo" role="img" aria-label="Photo of a businessman working on a laptop in an airport lounge"></div>
<div class="abs num" style="left:642px;top:786px">01</div>
<div class="abs kicker" style="left:744px;top:783px">LIFESTYLE CLUB</div>
<h2 class="abs heading" style="left:744px;top:806px">ABOUT VELMOR</h2>
<div class="abs about-copy">
  <p>VELMOR is a members only lifestyle club founded in order to bring the best services, experiences, and opportunities to our diverse community of members.</p>
  <p>Our members consist of creatives, athletes, artists, and other professionals.</p>
</div>
<div class="abs btn" style="left:642px;top:1070px;width:145px;height:48px">JOIN NOW
  <svg width="16" height="16" viewBox="0 0 16 16" aria-hidden="true"><circle cx="8" cy="8" r="8" fill="#fff"/><path d="M5 8h6M8.5 5l3 3-3 3" stroke="#8e0f80" stroke-width="2" fill="none"/></svg>
</div>

<div class="abs benefits-band" role="img" aria-label="Dark photo of members socialising at an event"></div>
<div class="abs pink-band" role="img" aria-label="Faint photo of friends laughing together"></div>
<div class="abs badge"><span class="num" style="margin-top:-20px">02</span></div>
<div class="abs center kicker" style="top:1356px;font-weight:400">ORGANIZES &amp; SUPPORTS</div>
<h2 class="abs center heading" style="top:1390px;color:#fff">BENEFITS &amp; SERVICES</h2>
<p class="abs center" style="top:1462px;font-size:14px;line-height:28px;color:#fff">VELMOR organizes and supports a ton of private events and parties for our members. Members are also provided access to<br>exclusive venues and events from our partners. Network with other members to build lasting relationships.</p>

<div class="abs grid">
  <div class="cell"><div class="cell-icon" role="img" aria-label="Airplane icon"></div><h3>FLIGHT TRAVEL</h3><p>Lorem ipsum dolor consectetur adipiscing elit,<br>sed do eiusmod tempor incididunt</p></div>
  <div class="cell"><div class="cell-icon" role="img" aria-label="Dumbbell icon"></div><h3>LUXURY GYM</h3><p>Lorem ipsum dolor consectetur adipiscing elit,<br>sed do eiusmod tempor incididunt</p></div>
  <div class="cell"><div class="cell-icon" role="img" aria-label="Disco ball and music icon"></div><h3>PRIVATE SOCIAL CLUBS</h3><p>Lorem ipsum dolor consectetur adipiscing elit,<br>sed do eiusmod tempor incididunt</p></div>
  <div class="cell"><div class="cell-icon" role="img" aria-label="Investment growth icon"></div><h3>PRIVATE INVESTMENT</h3><p>Lorem ipsum dolor consectetur adipiscing elit,<br>sed do eiusmod tempor incididunt</p></div>
  <div class="cell"><div class="cell-icon" role="img" aria-label="Attorneys icon"></div><h3>ATTORNEYS</h3><p>Lorem ipsum dolor consectetur adipiscing elit,<br>sed do eiusmod tempor incididunt</p></div>
  <div class="cell"><div class="cell-icon" role="img" aria-label="House in hand icon"></div><h3>REAL ESTATE AGENTS</h3><p>Lorem ipsum dolor consectetur adipiscing elit,<br>sed do eiusmod tempor incididunt</p></div>
</div>

<div class="abs center num" style="top:2088px">03</div>
<div class="abs center kicker" style="top:2170px">TO BUILD LASTING RELATIONSHIPS</div>
<h2 class="abs center heading" style="top:2201px">JOIN US &amp; EXPERIENCE A BETTER WAY</h2>
<p class="abs center" style="top:2274px;font-size:14px;line-height:28px;color:var(--text)">VELMOR organizes and supports a ton of private events and parties for our members. Members are also provided access to exclusive<br>venues and events from our partners. Network with other members to build lasting relationships.</p>
<div class="abs btn" style="left:510px;top:2363px;width:180px;height:48px">JOIN NOW
  <svg width="16" height="16" viewBox="0 0 16 16" aria-hidden="true"><circle cx="8" cy="8" r="8" fill="#fff"/><path d="M5 8h6M8.5 5l3 3-3 3" stroke="#8e0f80" stroke-width="2" fill="none"/></svg>
</div>

<footer class="abs footer"></footer>
<div class="abs socials" aria-label="Social links">
  <div class="social"></div><div class="social"></div><div class="social active"></div><div class="social"></div><div class="social"></div>
</div>
<nav class="abs center foot-links"><span>HOME</span><span>ABOUT</span><span>SERVICES AND BENEFITS</span><span>APPLY</span><span>CONTACT</span><span>PRIVACY POLICY</span></nav>
<p class="abs center copyright">Copyrights © 2018 Velmor. All Rights Reserved &nbsp;&nbsp;|&nbsp;&nbsp; Site Map.</p>

</body>
</html>
```